Ridgeline Journeys business card

please see website
www.ridgelinejourneys.comau

info needed on card
Curtis Halvey
Ph
email
Adventure Riding GPS trails

please use my logo and colours off my site

Curtis Halvey
curtis@ridgelinejourneys.com

```html
<!DOCTYPE html>
<html lang="en">
<head>
<meta charset="utf-8">
<title>Ridgeline Journeys business card</title>
<link rel="stylesheet" href="https://fonts.googleapis.com/css2?family=Source+Sans+3:ital,wght@0,400;0,600;0,700;1,400&display=swap">
<style>
  :root {
    --backdrop: #4b4b4b;
    --card-light: #f4f4f4;
    --card-dark: #000000;
    --ink: #1c1c1c;
    --ink-soft: #444444;
    --rule: #c8c8c8;
    --yellow: #f5c800;
    --yellow-bright: #fbe21c;
  }
  * { margin: 0; padding: 0; box-sizing: border-box; }
  html, body { width: 1200px; height: 750px; overflow: hidden; }
  body {
    background: var(--backdrop);
    font-family: "Source Sans 3", Arial, sans-serif;
    position: relative;
  }
  .card {
    position: absolute;
    left: 371px;
    width: 462px;
    height: 263px;
    overflow: hidden;
  }
  .card--front { top: 99px; background: var(--card-light); }
  .card--back { top: 381px; background: var(--card-dark); }

  .brand {
    position: absolute;
    left: 40px;
    top: 99px;
    width: 172px;
    display: flex;
    align-items: center;
    gap: 10px;
  }
  .brand__dot {
    width: 22px; height: 22px;
    border-radius: 50%;
    background: var(--yellow);
    flex: none;
  }
  .brand__name {
    font-weight: 700;
    font-size: 21px;
    line-height: 22px;
    color: var(--ink);
    letter-spacing: 0.2px;
  }
  .brand__name span { display: block; white-space: nowrap; }
  .divider {
    position: absolute;
    left: 229px; top: 83px;
    width: 1px; height: 80px;
    background: var(--rule);
  }
  .contact {
    position: absolute;
    left: 246px; top: 82px;
  }
  .contact__name {
    font-weight: 600;
    font-size: 17px;
    color: var(--ink);
    margin-bottom: 5px;
  }
  .contact__line {
    display: flex;
    align-items: center;
    gap: 6px;
    font-size: 11px;
    color: var(--ink-soft);
    height: 17.5px;
    white-space: nowrap;
  }
  .contact__line svg { width: 11px; height: 11px; flex: none; }

  .front-band {
    position: absolute;
    left: 0; bottom: 0;
    width: 100%; height: 17px;
  }

  .back-brand {
    position: absolute;
    left: 0; right: 0; top: 118px;
    display: flex;
    justify-content: center;
    align-items: center;
    gap: 12px;
  }
  .back-brand__dot {
    width: 22px; height: 22px;
    border-radius: 50%;
    background: var(--yellow);
  }
  .back-brand__name {
    font-weight: 700;
    font-size: 30px;
    color: #ffffff;
  }
  .tagline {
    position: absolute;
    left: 0; right: 0; top: 214px;
    text-align: center;
    font-style: italic;
    font-size: 13px;
    color: var(--yellow-bright);
  }
</style>
</head>
<body>
  <section class="card card--front" aria-label="Card front">
    <div class="brand">
      <span class="brand__dot"></span>
      <p class="brand__name"><span>Ridgeline</span><span>Journeys</span></p>
    </div>
    <div class="divider"></div>
    <div class="contact">
      <p class="contact__name">Curtis Halvey</p>
      <p class="contact__line">
        <svg viewBox="0 0 12 12" aria-hidden="true"><path d="M2.4 0.8l2 2.2-1 1.4c.6 1.5 1.8 2.7 3.2 3.3l1.4-1 2.2 2-1.2 2C5.6 10.5 1.5 6.4 .6 2z" fill="#1c1c1c"/></svg>
        612 508 3941
      </p>
      <p class="contact__line">
        <svg viewBox="0 0 12 12" aria-hidden="true"><rect x="0.5" y="2.5" width="11" height="7.5" fill="#1c1c1c"/><path d="M0.8 3l5.2 3.8L11.2 3" stroke="#f4f4f4" stroke-width="1" fill="none"/></svg>
        curtis@ridgelinejourneys.com
      </p>
      <p class="contact__line">
        <svg viewBox="0 0 12 12" aria-hidden="true"><circle cx="6" cy="6" r="5.5" fill="#1c1c1c"/><path d="M3 3.5c1 .3 1.5 1.2 1.2 2.2s.8 1.8 1.6 1.4M7.5 1.5c-.3 1.2.8 1.6 1.8 1.4M8 8.5c.7-.5 1.5-.3 2 .3" stroke="#f4f4f4" stroke-width="0.9" fill="none"/></svg>
        www.ridgelinejourneys.com.au
      </p>
    </div>
    <svg class="front-band" viewBox="0 0 462 17" preserveAspectRatio="none" aria-hidden="true">
      <defs>
        <linearGradient id="bandYellow" x1="0" x2="1" y1="0" y2="0">
          <stop offset="0" stop-color="#f5c400"/>
          <stop offset="1" stop-color="#fbe21c"/>
        </linearGradient>
      </defs>
      <polygon points="0,0 300,0 295,17 0,17" fill="#000"/>
      <polygon points="301,0 304,0 299,17 296,17" fill="#ffffff"/>
      <polygon points="305,0 462,0 462,17 300,17" fill="url(#bandYellow)"/>
    </svg>
  </section>

  <section class="card card--back" aria-label="Card back">
    <div class="back-brand">
      <span class="back-brand__dot"></span>
      <span class="back-brand__name">Ridgeline Journeys</span>
    </div>
    <p class="tagline">Adventure Riding GPS trails</p>
  </section>
</body>
</html>
```